Business card for law firm

Need business card for new law firm. Think confident, authoritative, conservative, but not stuffy or old-fashioned.

Contact Information for Business Card

Content for card - logo (uploaded), plus the following:

Paul Whitcombe (larger font)
Managing Partner (larger font, but not as large as name)
Level 9, 7 Ferris Lane
Sydney NSW 2000
Main Tel 02 9364 2710
Direct Tel 02 8472 3159
Email paul@qvlegal.com.au
www.qvlegal.com.au

Letterhead design should include logo plus:
Level 9, 7 Ferris Lane
Sydney NSW 2000
Tel 02 8472 3159
www.qvlegal.com.au

```html
<!DOCTYPE html>
<html lang="en">
<head>
<meta charset="utf-8">
<title>Quayvale Legal – Business Card</title>
<link href="https://fonts.googleapis.com/css2?family=Open+Sans:wght@400;600;700&display=swap" rel="stylesheet">
<style>
  :root {
    --backdrop: #8c8c8c;
    --card: #fbfbfb;
    --navy: #15205e;
    --ink: #2a2a2a;
    --muted: #4a4a4a;
  }
  * { margin: 0; padding: 0; box-sizing: border-box; }
  html, body {
    width: 1200px; height: 848px; overflow: hidden;
    background: var(--backdrop);
    font-family: "Open Sans", Arial, sans-serif;
  }
  .sheet {
    width: 1200px; height: 848px;
    display: flex; align-items: center; justify-content: center; gap: 48px;
  }
  .card {
    position: relative;
    width: 540px; height: 310px;
    background: var(--card);
    box-shadow: 0 6px 18px rgba(0,0,0,0.18);
  }

  /* contact side */
  .brand-block {
    position: absolute; left: 34px; top: 30px;
    display: flex; flex-direction: column; align-items: flex-start; gap: 12px;
  }
  .brand-square {
    width: 170px; height: 170px; background: var(--navy);
  }
  .brand-name-small {
    font-weight: 600; font-size: 15px; letter-spacing: 3px;
    color: var(--navy); text-transform: uppercase;
  }
  .contact {
    position: absolute; right: 34px; bottom: 28px;
    text-align: right; line-height: 1.35;
  }
  .contact .person {
    font-weight: 700; font-size: 24px; color: var(--navy); line-height: 1.1;
  }
  .contact .role {
    font-weight: 700; font-size: 16px; color: var(--ink); margin-bottom: 8px;
  }
  .contact .line { font-size: 13px; color: var(--muted); }
  .contact .gap { margin-top: 6px; }
  .contact .web { font-weight: 600; color: var(--ink); margin-top: 2px; }

  /* brand side */
  .brand-face {
    display: flex; align-items: center; justify-content: center; gap: 16px;
  }
  .brand-face .brand-mark {
    width: 30px; height: 30px; background: var(--navy);
  }
  .brand-face .brand-name {
    font-weight: 600; font-size: 34px; letter-spacing: 5px;
    color: var(--ink); text-transform: uppercase;
  }
</style>
</head>
<body>
  <main class="sheet">
    <section class="card card--contact">
      <div class="brand-block">
        <div class="brand-square"></div>
        <div class="brand-name-small">Quayvale Legal</div>
      </div>
      <div class="contact">
        <p class="person">Paul Whitcombe</p>
        <p class="role">Managing Partner</p>
        <p class="line">Level 9, 7 Ferris Lane</p>
        <p class="line">Sydney NSW 2000</p>
        <p class="line gap">02 9364 2710 (Main)</p>
        <p class="line">02 8472 3159 (Direct)</p>
        <p class="line">paul@qvlegal.com.au</p>
        <p class="line web">www.qvlegal.com.au</p>
      </div>
    </section>

    <section class="card card--brand brand-face">
      <div class="brand-mark"></div>
      <p class="brand-name">Quayvale Legal</p>
    </section>
  </main>
</body>
</html>
```